WTF!!! We need a modern professional website for a business litigation law firm.

We need a modern, clean, professional and uncomplicated website for a new business trial and litigation law firm called "Haverlock Trial Firm PLLC". Website must be mobile optimized for iPad and smartphone. The law firm specializes in counseling and representing large corporations, small businesses and entrepreneurs in and out of the courtroom. Lawyers in the firm serve as Florida counsel and trial counsel to organizations facing claims involving product liability, premises liability, professional liability, vehicle and transportation liability, warranty claims, construction defects and delay claims, complex business disputes, commercial litigation and bid disputes in State and Federal Courts. The website is mainly to provide information about the firm, and should include sections describing the firm, identifying the Industries Served and Areas of Practice ," a separate page identifying the "Professionals", a separate page for "Resources & Advisories," and a traveling "Connect With Us" button a site visitor can click on that will launch an email to the Firm's general email account. The website should allow us to easily modify the content on these pages, and let us add/modify links to external information sources. We will not sell anything or take payments through the website. We do need to be able to easily upload and update photographs of attorneys and add new attorneys names/email hyperlinks as the firm grows. We would like to add developments in the law or success stories easily and quickly, such as through a blog page. On the "Connect With Us" page the website should have hyperlinks to email the Firm, and there should be hyperlinks to email each professional on the "Professionals" page. The website should be viewable on mobile devices without distortion. The law firm focuses on trial work and should have some imagery associated with courtrooms, but the overall theme of the site should be modern, clean, and communicate sophistication and strength. The website should be made in Wordpress. We have uploaded logo files for Haverlock Trial Firm.

Target Market(s)

Corporations and companies that are looking for legal representation. Other attorneys/legal industry.

Industry/Entity Type

Legal Industry

Coding

Coded - Design and coding required

Number of Pages Required

1 page

Font styles to use
Sans Serif

Requirements
Must have
• Simple, clean, sophisticated, modern website that includes the logo, watermark of logo, and the elements described above.
Nice to have
• Pictures of city scape, buildings, courtroom, team members.

```html
<!DOCTYPE html>
<html lang="en">
<head>
<meta charset="utf-8">
<title>Haverlock Trial Firm PLLC</title>
<link href="https://fonts.googleapis.com/css2?family=Lato:wght@400;700;900&display=swap" rel="stylesheet">
<style>
:root{
  --navy:#0d2f6b;
  --navy-deep:#0a2456;
  --ink:#1b1b1b;
  --muted:#555;
  --line:#e3e3e3;
  --black:#050505;
  --star:#f29a1f;
  --white:#ffffff;
}
*{box-sizing:border-box;margin:0;padding:0}
html,body{width:1200px;height:4125px;overflow:hidden}
body{font-family:'Lato',sans-serif;color:var(--ink);background:#fff;position:relative}
.abs{position:absolute}
a{color:inherit;text-decoration:none}

.topbar{left:0;top:0;width:1200px;height:29px;background:var(--navy-deep);color:#fff;font-size:12px}
.topbar span{position:absolute;top:7px}
.nav{left:0;top:29px;width:1200px;height:64px;background:#fff;font-size:15px;box-shadow:0 1px 4px rgba(0,0,0,.08);z-index:2}
.nav a{position:absolute;top:24px}
.nav a.active{color:var(--navy);font-weight:700}
.nav a.active:after{content:"";position:absolute;left:0;right:0;bottom:-5px;height:2px;background:var(--navy)}
.logo-tab{left:516px;top:0;width:170px;height:135px;z-index:3}
.brand{position:absolute;left:0;width:170px;text-align:center;font-weight:900;color:var(--navy-deep);line-height:1}
.brand.name{top:66px;font-size:22px}
.brand.sub{top:92px;font-size:10px;letter-spacing:2px}
.brand-mark{position:absolute;left:67px;top:20px;width:36px;height:36px;background:var(--navy-deep)}

.hero{left:0;top:93px;width:1200px;height:630px}
.hero h1{left:108px;top:127px;width:660px;font-size:45px;line-height:52px;font-weight:700;color:#fff}
.hero p{left:110px;top:299px;width:470px;font-size:20px;line-height:26px;color:#fff}
.btn{background:var(--navy);color:#fff;font-size:15px;display:flex;align-items:center;justify-content:center}

.section-title{left:0;width:1200px;text-align:center;font-size:40px;font-weight:700;color:var(--ink)}
.section-title b{color:var(--navy);font-weight:700}
.section-title:after{content:"";display:block;width:52px;height:4px;background:var(--navy);margin:10px auto 0}
.section-title.light,.section-title.light b{color:#fff}
.section-title.light:after{background:#fff}

.card-img{border-radius:2px}
.card h3{font-size:21px;font-weight:700;margin:20px 0 16px;line-height:25px}
.card p{font-size:14px;line-height:22px;color:var(--muted)}
.card .more{display:block;margin-top:14px;font-size:14px;font-weight:700;color:var(--navy)}
.arrow{width:32px;height:32px;border-radius:50%;background:var(--navy)}

.about-photo{left:112px;top:1378px;width:490px;height:499px;box-shadow:0 6px 18px rgba(0,0,0,.2)}
.about-title{left:695px;top:1368px;font-size:40px;font-weight:700;color:var(--navy)}
.about-title:after{content:"";display:block;width:52px;height:4px;background:var(--navy);margin-top:6px}
.about-text{left:695px;top:1460px;width:395px;font-size:15.5px;line-height:25px;color:var(--muted)}
.about-text p+p{margin-top:25px}

.industry{width:300px;text-align:center;color:#fff}
.industry h3{font-size:23px;font-weight:700;margin:8px 0 12px}
.industry p{font-size:14px;line-height:25.5px}
.industry svg{display:block;margin:0 auto}

.testi{width:318px;height:228px;border:1px solid var(--line);border-radius:6px;padding:28px 24px;background:#fff}
.testi.active{background:var(--navy);border-color:var(--navy);color:#fff}
.testi .stars{color:var(--star);font-size:15px;letter-spacing:1px}
.testi.active .stars{color:#fff}
.testi p{margin-top:16px;font-size:14px;line-height:22px;color:var(--muted)}
.testi.active p{color:#fff}
.testi h4{margin-top:18px;font-size:17px;font-weight:700}
.testi small{display:block;margin-top:8px;font-size:12px;color:var(--muted)}
.testi.active small{color:#fff}

.footer{left:0;top:3532px;width:1200px;height:593px}
.footer-col{top:3800px;color:var(--white)}
.footer-col h4{font-size:20px;font-weight:700;margin-bottom:22px;color:var(--white)}
.footer-col p,.footer-col li{font-size:14px;line-height:24px;color:var(--white)}
.footer-col ul{list-style:none}
.footer-col li{margin-bottom:14.5px}
.contact-row{display:flex;align-items:flex-start;gap:18px;margin-bottom:22px;font-size:14px;line-height:26px;color:var(--white)}
.social{width:34px;height:34px;border:1.5px solid #fff;border-radius:6px}
</style>
</head>
<body>

<div class="abs topbar">
  <span style="left:112px">&#9719;&nbsp; Monday - Saturday : 8 Am - 5:30 PM &nbsp;&nbsp;&nbsp;&nbsp; Sunday : Closed</span>
  <span style="left:740px">&#9742;&nbsp; +1 555 010 0188 &nbsp;&nbsp;&nbsp; &#9993;&nbsp; info@haverlocktrialfirm.com</span>
</div>

<nav class="abs nav">
  <a class="active" style="left:114px">Home</a>
  <a style="left:179px">About Us</a>
  <a style="left:266px">Practice Areas</a>
  <a style="left:387px">Professionals</a>
  <a style="left:733px">Resources &amp; Advisories</a>
  <a style="left:914px">Industries Served</a>
  <a style="left:1057px">Blog</a>
</nav>

<div class="abs logo-tab">
  <svg width="170" height="135" class="abs" style="left:0;top:0"><path d="M0 0H170V112L85 135L0 112Z" fill="#fff"/></svg>
  <div class="brand-mark"></div>
  <div class="brand name">HAVERLOCK</div>
  <div class="brand sub">TRIAL FIRM</div>
</div>

<section class="abs hero">
  <svg width="1200" height="630" class="abs" style="left:0;top:0">
    <defs><linearGradient id="heroGrad" x1="0" y1="0" x2="1" y2="0.4">
      <stop offset="0" stop-color="#4a6a87"/><stop offset=".5" stop-color="#6d6a66"/><stop offset="1" stop-color="#8a7a68"/>
    </linearGradient></defs>
    <rect width="1200" height="630" fill="url(#heroGrad)" role="img" aria-label="Photo of two business professionals in suits reviewing documents together"/>
    <path d="M0 540L600 627L1200 540V630H0Z" fill="#fff"/>
    <path d="M0 540L600 628L1200 540" stroke="#0d2f6b" stroke-width="14" fill="none"/>
  </svg>
  <h1 class="abs">DEFENDING YOUR BUSINESS WITH STRENGTH AND EXPERTISE</h1>
  <p class="abs">Representing corporations, small businesses, and entrepreneurs in complex litigation matters across Florida’s courts.</p>
  <a class="abs btn" style="left:110px;top:404px;width:155px;height:37px">Connect With Us</a>
</section>

<h2 class="abs section-title" style="top:800px">AREAS OF <b>PRACTICE</b></h2>
<div class="abs arrow" style="left:56px;top:977px"><svg width="32" height="32"><path d="M18 10l-6 6 6 6" stroke="#fff" stroke-width="2.5" fill="none"/></svg></div>
<div class="abs arrow" style="left:1110px;top:977px"><svg width="32" height="32"><path d="M14 10l6 6-6 6" stroke="#fff" stroke-width="2.5" fill="none"/></svg></div>

<article class="abs card" style="left:110px;top:886px;width:313px">
  <div class="card-img" role="img" aria-label="Hands holding a product liability insurance document" style="height:213px;background:linear-gradient(135deg,#3a3a3a,#cfcfcf)"></div>
  <h3>Product Liability</h3>
  <p>We represent businesses facing claims related to defective products, ensuring that companies are protected from unwarranted claims while maintaining consumer safety.</p>
  <a class="more">Read More ...</a>
</article>
<article class="abs card" style="left:443px;top:886px;width:313px">
  <div class="card-img" role="img" aria-label="Hand holding a premises liability card" style="height:213px;background:linear-gradient(135deg,#d8d8d8,#9aa0a6)"></div>
  <h3>Premises Liability</h3>
  <p>Our team defends businesses in cases involving accidents on their property, from slip-and-fall incidents to more complex liability issues.</p>
  <a class="more">Read More ...</a>
</article>
<article class="abs card" style="left:775px;top:886px;width:313px">
  <div class="card-img" role="img" aria-label="Professionals shaking hands in a bright office" style="height:213px;background:linear-gradient(135deg,#6c7580,#e6e8ea)"></div>
  <h3>Professional Liability</h3>
  <p>We provide strong legal counsel to professionals, including attorneys, architects, and healthcare providers, in matters of negligence and malpractice claims.</p>
  <a class="more">Read More ...</a>
</article>

<div class="abs about-photo" role="img" aria-label="Attorney working at a laptop in a modern office" style="background:linear-gradient(160deg,#c9cdd1,#7d8896 60%,#2c3b55)"></div>
<h2 class="abs about-title">ABOUT US</h2>
<div class="abs about-text">
  <p>Lorem ipsum dolor sit amet, consectetur adipiscing elit, sed do eiusmod tempor incididunt ut labore et dolore magna aliqua. Quis ipsum suspendisse ultrices gravida. Risus commodo viverra maecenas accumsan lacus vel facilisis.</p>
  <p>Sed ut perspiciatis unde omnis iste natus error sit volup accusantium doloremque laudantium, totam rem aper, eaque ipsa quae ab illo inventore veritatis et quasi archi ecto beatae vitae dicta sunt explicabo. Sed ut perspi ciatis unde omnis iste natus error sit voluptatem accu santium doloremque laudantium, totam rem aperiam, eaque ipsa quae ab illo inventore veritatis et quasi dicta sunt explicabo.</p>
</div>
<a class="abs btn" style="left:695px;top:1838px;width:120px;height:38px">Read More</a>

<svg class="abs" width="1200" height="635" style="left:0;top:1922px">
  <defs><linearGradient id="indGrad" x1="0" y1="0" x2="0" y2="1">
    <stop offset="0" stop-color="#123a7a"/><stop offset="1" stop-color="#0b2a63"/>
  </linearGradient></defs>
  <path d="M0 0L600 93L1200 0V633L600 545L0 633Z" fill="url(#indGrad)"/>
</svg>
<h2 class="abs section-title light" style="top:2088px"><b>INDUSTRIES SERVED</b></h2>

<div class="abs industry" style="left:98px;top:2172px">
  <svg width="70" height="70" viewBox="0 0 70 70" fill="#fff"><circle cx="35" cy="20" r="13"/><circle cx="35" cy="20" r="5" fill="#0d2f6b"/><rect x="4" y="42" width="62" height="10" rx="2"/><rect x="4" y="56" width="62" height="10" rx="2"/></svg>
  <h3>Manufacturing</h3>
  <p>We represent manufacturers in disputes involving product defects, liability claims, warranty issues, and regulatory compliance.</p>
</div>
<div class="abs industry" style="left:450px;top:2172px">
  <svg width="70" height="70" viewBox="0 0 70 70" fill="#fff"><rect x="10" y="8" width="34" height="18" rx="3" transform="rotate(12 27 17)"/><rect x="4" y="34" width="14" height="14"/><rect x="24" y="32" width="26" height="26" rx="2"/><path d="M50 40h10l6 8v10H50z"/><circle cx="32" cy="62" r="5"/><circle cx="58" cy="62" r="5"/></svg>
  <h3>Transportation &amp; Logistics</h3>
  <p>We offer strategic counsel to businesses in the transportation sector, including trucking, shipping, and logistics companies, on matters such as ..</p>
</div>
<div class="abs industry" style="left:802px;top:2172px">
  <svg width="70" height="70" viewBox="0 0 70 70" fill="#fff"><path d="M10 34a25 25 0 0 1 50 0z"/><rect x="6" y="34" width="58" height="7" rx="2"/><circle cx="35" cy="54" r="12"/><circle cx="35" cy="54" r="5" fill="#0d2f6b"/></svg>
  <h3>Construction</h3>
  <p>Our firm specializes in defending construction companies against claims related to delays, defects, accidents, and contractual disputes.</p>
</div>

<h2 class="abs section-title" style="top:2545px">OUR <b>TESTIMONIALS</b></h2>
<div class="abs testi" style="left:110px;top:2630px"><div class="stars">★★★★★</div><p>Excepteur sint occaecat cupidatat non proident, sunt in culpa qui officia deserunt mollit anim id est laborum.</p><h4>Whitmore</h4><small>Jan 20 2024</small></div>
<div class="abs testi active" style="left:441px;top:2630px"><div class="stars">★★★★★</div><p>Excepteur sint occaecat cupidatat non proident, sunt in culpa qui officia deserunt mollit anim id est laborum.</p><h4>Mara</h4><small>Jan 20 2024</small></div>
<div class="abs testi" style="left:771px;top:2630px"><div class="stars">★★★★★</div><p>Excepteur sint occaecat cupidatat non proident, sunt in culpa qui officia deserunt mollit anim id est laborum.</p><h4>Gwendolyn</h4><small>Jan 20 2024</small></div>
<svg class="abs" width="50" height="6" style="left:550px;top:2882px"><rect width="13" height="5" rx="2" fill="#0d2f6b"/><rect x="17" width="13" height="5" rx="2" fill="#c8c8c8"/><rect x="34" width="13" height="5" rx="2" fill="#c8c8c8"/></svg>

<h2 class="abs section-title" style="top:2968px">SUCCESS <b>STORIES</b></h2>
<div class="abs arrow" style="left:56px;top:3143px"><svg width="32" height="32"><path d="M18 10l-6 6 6 6" stroke="#fff" stroke-width="2.5" fill="none"/></svg></div>
<div class="abs arrow" style="left:1110px;top:3143px"><svg width="32" height="32"><path d="M14 10l6 6-6 6" stroke="#fff" stroke-width="2.5" fill="none"/></svg></div>

<article class="abs card" style="left:110px;top:3050px;width:313px">
  <div class="card-img" role="img" aria-label="Smiling professional seated at a meeting table" style="height:213px;background:linear-gradient(135deg,#4f5962,#b9bcc0)"></div>
  <h3>Defending a Major Manufacturer in a Product Liability Case</h3>
  <p>Lorem ipsum dolor sit amet, consectetur adipiscing elit, sed do eiusmod tempor incididunt ut labore et dolore magna aliqua.</p>
  <a class="more">Read More ...</a>
</article>
<article class="abs card" style="left:442px;top:3050px;width:313px">
  <div class="card-img" role="img" aria-label="Hand signing a document with a pen" style="height:213px;background:linear-gradient(135deg,#8a8580,#3b3835)"></div>
  <h3>Defending a Healthcare Provider in a Malpractice Lawsuit</h3>
  <p>Lorem ipsum dolor sit amet, consectetur adipiscing elit, sed do eiusmod tempor incididunt ut labore et dolore magna aliqua.</p>
  <a class="more">Read More ...</a>
</article>
<article class="abs card" style="left:773px;top:3050px;width:313px">
  <div class="card-img" role="img" aria-label="Hands reviewing paperwork beside a laptop" style="height:213px;background:linear-gradient(135deg,#d7dde3,#6e7f92)"></div>
  <h3>Winning a Bid Dispute for a State Government Contract</h3>
  <p>Lorem ipsum dolor sit amet, consectetur adipiscing elit, sed do eiusmod tempor incididunt ut labore et dolore magna aliqua.</p>
  <a class="more">Read More ...</a>
</article>

<footer class="abs footer">
  <svg class="abs" width="1200" height="593" style="left:0;top:0">
    <path d="M0 88L600 0L1200 88V593H0Z" fill="var(--navy)"/>
    <path d="M0 88L600 22L1200 88V593H0Z" fill="var(--black)"/>
    <line x1="114" y1="550" x2="1088" y2="550" stroke="#333" stroke-width="1"/>
  </svg>
  <div class="abs" style="left:0;top:152px;width:1200px;text-align:center;color:#fff;font-weight:900;line-height:1">
    <div style="font-size:34px">HAVERLOCK</div>
    <div style="font-size:14px;letter-spacing:4px;margin-top:6px">TRIAL FIRM</div>
  </div>
  <div class="abs" style="left:0;top:572px;width:1200px;text-align:center;color:#fff;font-size:12px">Copyright © 2025 Haverlock Trial Firm PLLC. All rights reserved.</div>
</footer>

<div class="abs footer-col" style="left:114px;width:260px">
  <h4>About Us</h4>
  <p style="line-height:24.5px">Lorem ipsum dolor sit amet, consec adipiscing elit, sed do eiusmod tem incididunt ut labore et dolore magna aliqua.</p>
  <div style="display:flex;gap:14px;margin-top:28px">
    <div class="social" role="img" aria-label="Social profile link" style="background:var(--navy);border-color:var(--navy)"></div>
    <div class="social" role="img" aria-label="Social profile link"></div>
    <div class="social" role="img" aria-label="Social profile link"></div>
    <div class="social" role="img" aria-label="Social profile link"></div>
  </div>
</div>

<div class="abs footer-col" style="left:416px;width:290px">
  <h4>Contact Us</h4>
  <div class="contact-row"><svg width="22" height="24" viewBox="0 0 22 24"><path d="M11 22s7-7 7-12a7 7 0 0 0-14 0c0 5 7 12 7 12z" stroke="#fff" stroke-width="1.6" fill="none"/><circle cx="11" cy="10" r="2.5" stroke="#fff" stroke-width="1.4" fill="none"/></svg><span>123, Haverlock Trial Firm<br>PLLC Company Na 12456.</span></div>
  <div class="contact-row"><svg width="22" height="22" viewBox="0 0 22 22"><path d="M5 3l4 4-2 3c1.5 3 3 4.5 5 5l3-2 4 4-3 3C9 20 2 13 2 6z" stroke="#fff" stroke-width="1.5" fill="none"/></svg><span>+1 555 010 0188</span></div>
  <div class="contact-row"><svg width="22" height="22" viewBox="0 0 22 22"><rect x="2" y="5" width="18" height="13" stroke="#fff" stroke-width="1.5" fill="none"/><path d="M2 6l9 7 9-7" stroke="#fff" stroke-width="1.5" fill="none"/></svg><span>info@haverlocktrialfirm.com</span></div>
</div>

<div class="abs footer-col" style="left:735px;width:180px">
  <h4>Quick Links</h4>
  <ul><li>Home</li><li>About Us</li><li>Practice Areas</li><li>Professionals</li><li>Industries Served</li></ul>
</div>

<div class="abs footer-col" style="left:932px;width:200px">
  <h4>Other Links</h4>
  <ul><li>Resources &amp; Advisories</li><li>Blog</li><li>Contact Us</li><li>Privacy Policy</li><li>Terms of Service</li></ul>
</div>

</body>
</html>
```